KTWG application splash screen

We need a 1024x768 image for use as an application splash screen.
The image will be displayed full screen on an 10 inch industrial PC 1024x768 screen while our application is launching. The image should convey that the application is "Waiting for connection to Wi-Fi access point..." and include a graphic of the industrial PC connected to the access point via an Ethernet cable. A list of troubleshooting steps should be included at the bottom of the image. The troubleshooting steps should not be the main focus of the image and should be shown in a smaller font (but still readable at 1024x768 displayed on a 10 inch screen).
I will include a mock up of the general idea of what we are looking for as well as image files for the industrial PC, a screenshot of our application to show on the PC's screen and the AP.
For general look and feel and a sense of corporate branding please review our website https://marrowgatesoilworks.example/. The splash screen should reflect corporate branding.
Target Market(s)
Users of our application
Industry/Entity Type
Agriculture
Look and feel

```html
<!DOCTYPE html>
<html lang="en">
<head>
<meta charset="utf-8">
<title>KTWG splash screen – waiting for Wi-Fi</title>
<link rel="stylesheet" href="https://fonts.googleapis.com/css2?family=Didact+Gothic&family=Poppins:wght@600;700&display=swap">
<style>
  :root {
    --stage: #595959;
    --paper-light: #ffffff;
    --paper-mid: #f1f1f1;
    --paper-dark: #d9d8d9;
    --ink: #1f1f1f;
    --ink-soft: #3a3a3a;
    --brand-green: #2fb36a;
    --device-dark: #262626;
    --device-screen: #cfe9d7;
    --ap-white: #eeeeee;
  }
  * { box-sizing: border-box; margin: 0; padding: 0; }
  html, body {
    width: 1200px; height: 1114px; overflow: hidden;
    background: var(--stage);
  }
  .splash {
    position: absolute; left: 0; top: 139px;
    width: 1200px; height: 835px;
    background: linear-gradient(125deg, var(--paper-light) 0%, var(--paper-mid) 45%, var(--paper-dark) 100%);
    font-family: "Didact Gothic", "Poppins", sans-serif;
    color: var(--ink);
  }
  .wifi-icon { position: absolute; left: 554px; top: 70px; width: 92px; height: 62px; }
  .status-title {
    position: absolute; left: 0; top: 140px; width: 1200px;
    text-align: center; font-size: 37px; line-height: 46px; letter-spacing: 1px;
    font-weight: 400; color: var(--ink);
  }
  .device-pc {
    position: absolute; left: 124px; top: 272px; width: 337px; height: 250px;
    border-radius: 14px;
    background: radial-gradient(ellipse at 50% 45%, var(--device-screen) 0%, #8fb39a 45%, var(--device-dark) 62%);
  }
  .device-ap {
    position: absolute; left: 1038px; top: 266px; width: 29px; height: 207px;
    border-radius: 8px;
    background: linear-gradient(90deg, #d8d8d8, var(--ap-white) 45%, #cfcfcf);
  }
  .cable { position: absolute; left: 461px; top: 460px; width: 620px; height: 50px; }
  .label {
    position: absolute; font-family: "Poppins", sans-serif; font-weight: 600;
    font-size: 17px; letter-spacing: 0.3px; color: var(--ink); white-space: nowrap;
  }
  .label-cable { left: 505px; top: 505px; }
  .label-ap { left: 874px; top: 505px; }
  .label-pc { left: 168px; top: 535px; }
  .troubleshoot-badge {
    position: absolute; left: 124px; top: 587px; width: 261px; height: 30px;
    border-radius: 15px; background: var(--brand-green); color: #fff;
    font-family: "Poppins", sans-serif; font-weight: 700; font-size: 19px;
    line-height: 30px; padding-left: 20px;
  }
  .steps { position: absolute; left: 149px; top: 626px; list-style: none; font-size: 15px; color: var(--ink-soft); }
  .steps li { position: relative; padding-left: 15px; line-height: 23.5px; white-space: nowrap; }
  .steps li::before {
    content: ""; position: absolute; left: -1px; top: 8px;
    width: 9px; height: 9px; border-radius: 50%; background: var(--ink);
  }
  .steps .sub { list-style: none; margin-left: 23px; }
  .steps .sub li { padding-left: 21px; }
  .brand-name {
    position: absolute; left: 985px; top: 720px;
    font-family: "Poppins", sans-serif; font-weight: 700; font-size: 28px;
    color: var(--ink-soft); letter-spacing: 1px;
  }
</style>
</head>
<body>
  <main class="splash">
    <svg class="wifi-icon" viewBox="0 0 92 62" aria-hidden="true">
      <g fill="none" stroke="var(--brand-green)" stroke-width="9" stroke-linecap="butt">
        <path d="M6 22 A56 56 0 0 1 86 22"/>
        <path d="M21 36 A35 35 0 0 1 71 36"/>
      </g>
      <path d="M46 62 L33 50 A18 18 0 0 1 59 50 Z" fill="var(--brand-green)"/>
    </svg>

    <h1 class="status-title">Waiting for connection to<br>Wi-Fi access point...</h1>

    <div class="device-pc" role="img" aria-label="Industrial tractor cab computer displaying the seeding application with green bar chart"></div>

    <svg class="cable" viewBox="0 0 620 50" aria-hidden="true">
      <rect x="0" y="23" width="22" height="14" rx="2" fill="#1a1a1a"/>
      <rect x="22" y="25" width="10" height="10" fill="#444"/>
      <path d="M32 30 H582 Q592 30 592 20 V8" fill="none" stroke="#111" stroke-width="3.5"/>
    </svg>

    <div class="device-ap" role="img" aria-label="White outdoor Wi-Fi access point with green status light"></div>

    <span class="label label-cable">ETHERNET CABLE</span>
    <span class="label label-ap">WI-FI ACCESS POINT</span>
    <span class="label label-pc">TRACTOR CAB COMPUTER</span>

    <div class="troubleshoot-badge">Troubleshooting steps</div>
    <ul class="steps">
      <li>This screen should only be visible for a short time on boot.</li>
      <li>If this screen stays visible for more than a minute:
        <ul class="sub">
          <li>Verify that the Wi-Fi Access Point (AP) powers up when this system does (indicated by a green light on the side of the AP).</li>
          <li>Check the Ethernet cable between this system and the AP for damage, and replace it if necessary.</li>
          <li>Power-cycle this system and wait for it to reboot fully.</li>
          <li>If the issue persists, contact KTWG support for further assistance.</li>
        </ul>
      </li>
    </ul>

    <div class="brand-name">KTWG</div>
  </main>
</body>
</html>
```